Website development company website

ABOUT COMPANY
Hi everyone! We're a Melbourne, Australia website development company in a need of a website design that will make online store merchants want to engage our services.
We specialise exclusively in Torvista e-commerce platform (https://torvista-platform.example/). What distinguishes our business from competition is that rather than designing and building brand new websites, we offer development, support and maintenance services to established websites. Maintenance and Support are the keywords representing our business.
Our potential clients are people with broken, slow and underperforming Torvista installations who need assistance getting their websites up and making sales. Our website must pass the message that we can help, and provide quick means of making contact.
DESIGN
Overall, we're looking for a slick, clean, airy, conservative design. No need to do anything crazy, try to stick to what's "standard" in website design these days and make it easy on all of us. The website is unlikely to be updated too often so it needs to look attractive and fresh first time over and after a year, too.
Attached is our new logo, which you'll be able to take the basic idea from, the colors and fonts. Though, don't use the fonts from the logo in the website, stick to the standard widely supported fonts. Additional use of Google fonts is fine.
Don't overdo it with colors, stick to conservative basic color set and only use the colors from the log for accents like headings etc. Please, don't be tempted to use the blue and orange as background of whole blocks, other than perhaps footer. Thanks.
For the images used, I'd like to stay away from a design studio/digital agency feel and lean more towards professional support and maintenance services. I'm thinking images of content merchants doing their job. Something along the lines of "We'll be taking care of the website so that you only need to care about the business".
Some ideas I like:
http://www.plumframe-pics.example/detail/photo/portrait-of-confident-male-design-professional-royalty-free-image/572048163
http://www.plumframe-pics.example/detail/photo/designer-taking-picture-of-hat-high-res-stock-photography/839207514
http://www.plumframe-pics.example/detail/photo/woman-packaging-pottery-royalty-free-image/216684093
Images of colorful shopping bags and shopping carts are over the top and not serious enough. Instead of images matching Online Shopping, I'd try going more for Stability, Reliability, Performance.
Our existing website is http://www.bravuln.example. Please, don't take design ideas from it, but it will give you a picture of the structure of our new website and content that's going to be used initially.
If you could include a basic icon set to use throughout the website, that would be great. If the icons could match our logo (attached), it would be a big plus.
ALL PAGES
Every page must contain clearly visible phone number (1300 648 907) and a Contact Us Now button, which opens an AJAX driven popup form with Name, Email, Phone and Message to be sent through.
To start with, main menu items will be Torvista, Portfolio, Contact.
At the bottom of each page, please, include a newsletter subscription form with text Subscribe to Torvista Support and Security Updates.
For the footer, I'd like to see a logo strip with the following logos in grayscale (no need to link anywhere): Torvista, QRX, DataVane, NCB. You'll find the logos on Google Images.
Standard footer columns follow. Here, I'd like to see logos in color: Torvista Certified Developer, Torvista Ceritified Solution Provider. Again, the logos are on Google Images.
No social media logos/links necessary anywhere on the website.
...and then the copyright line.
FRONT PAGE
Large slider with images that would appeal to our target audience. Keywords here would be Torvista System Audit, Torvista Performance Optimisation, Torvista Website Emergency Recovery, Torvista Development Infrastructure Hosting. We'll have a static page created for each of these to link to.
In a corner of the slider, or on the edge, can I have an overlay with logos in color (same as footer): Torvista Certified Developer, Torvista Ceritified Solution Provider.
Underneath, a number of blocks, each with an image and teaser that we'll use to link to various pages throughout the website.
PORTFOLIO PAGE
I'm thinking a single long page with a block per client, which will contain project name, description from us and a testimonial from client. Also, each block will contain a single large screenshot. No gallery or slideshow is necessary here, just one image per project.
I'll leave the layout up to you, but try to put yourself in the shoes of a potential client reviewing our past work by simply scrolling down this one page.
CONTACT US PAGE
Separate page with the same form as above, phone number (1300 648 907), email address (support@kavreo.example), address (Suite 42, Level 3|8 Wattlebrook Lane|Fernvale Heights VIC 3999), and a grayscale Google Map.
CODING UP
Coding up into static HTML/CSS/JS is equally important as the design itself. We're a website development company, we'll be integrating the theme. We will spot any issues and we will point them out.
Coded up design must be fully responsive. Enough said.
To be able to create any content in future, we'd like one extra page coded up with samples of all themed elements, lists, forms, buttons, 2, 3, 4-column layout, alerts, icons, etc. This page does not need to be designed, only coded up.
The design will be integrated into Drupal using Twig. If possible at all, try to keep it in mind when designing and coding up, and make the integration into a Drupal theme easier for us.
GOOD LUCK!
That's it. Let me know if anything needs clarifying. So far I've had a great experience with ArtFlockly. I don't doubt some great designs will emerge. Clever ideas are highly appreciated, but also make it clear you've read and followed the points in this brief. Cheers, Tom

```html
<!DOCTYPE html>
<html lang="en">
<head>
<meta charset="utf-8">
<title>Kavreo E-Commerce – Torvista Support &amp; Maintenance</title>
<link rel="stylesheet" href="https://fonts.googleapis.com/css2?family=Open+Sans:wght@400;600;700&family=Roboto+Condensed:wght@400;700&display=swap">
<style>
:root{
  --navy:#0d3a6a;
  --orange:#e8801e;
  --ink:#1c1c1c;
  --text:#555;
  --grey-bg:#e9e9e9;
  --strip-bg:#e4e4e4;
  --dark-box:#262626;
  --pink:#e0127f;
  --white:#fff;
}
*{box-sizing:border-box;margin:0;padding:0}
html,body{width:1200px;height:2980px;overflow:hidden}
body{font-family:"Open Sans",Arial,sans-serif;color:var(--text);background:var(--white);position:relative}
.cond{font-family:"Roboto Condensed","Arial Narrow",sans-serif}
section,header,footer{position:absolute;left:0;width:1200px}
.btn{position:absolute;display:flex;align-items:center;justify-content:center;font-family:"Roboto Condensed","Arial Narrow",sans-serif;font-size:22px;color:var(--white);background:var(--orange);border-radius:4px;text-transform:uppercase}
.btn--navy{background:var(--navy)}

/* hero */
.hero{top:0;height:680px;overflow:hidden}
.hero__photo{position:absolute;inset:0;background:linear-gradient(100deg,#c9ccd0 0%,#e4e6e8 30%,#d7dbe0 55%,#9ea7b3 80%,#7d8796 100%)}
.hero__veil{position:absolute;inset:0;background:rgba(255,255,255,.35)}
.brand{position:absolute;left:78px;top:38px;display:flex;align-items:center;gap:14px}
.brand__mark{width:34px;height:44px;background:var(--orange);border-radius:3px}
.brand__name{font-family:"Open Sans",sans-serif;font-weight:700;font-size:40px;color:var(--orange);line-height:1}
.nav{position:absolute;right:90px;top:52px;display:flex;gap:48px;font-family:"Open Sans",sans-serif;font-size:21px;color:var(--ink)}
.nav a{color:inherit;text-decoration:none}
.nav .is-active{color:var(--navy)}
.hero__rule{position:absolute;left:78px;right:76px;top:130px;height:1px;background:rgba(255,255,255,.8)}
.hero__title{position:absolute;left:0;right:0;top:300px;text-align:center;font-weight:700;font-size:54px;line-height:64px;color:var(--navy)}
.hero__title b{color:#0b0b0b}
.hero .btn{left:492px;top:440px;width:218px;height:64px}

/* welcome */
.welcome{top:680px;height:420px}
.welcome__title{position:absolute;left:80px;top:48px;font-size:44px;line-height:52px;color:var(--navy)}
.welcome__title span{color:var(--orange)}
.welcome__text{position:absolute;left:80px;top:162px;width:560px;font-size:15px;line-height:24px}
.welcome__text p+p{margin-top:18px}
.welcome .btn{left:78px;top:306px;width:166px;height:64px}
.welcome__photo{position:absolute;left:698px;top:52px;width:412px;height:294px;background:linear-gradient(120deg,#5d6b80 0%,#9aa6b6 40%,#dfe3e8 70%,#f2f3f4 100%)}

/* services */
.services{top:1100px;height:570px;background:var(--grey-bg)}
.section-title{position:absolute;left:0;right:0;text-align:center;font-size:46px;color:var(--navy)}
.section-title span{color:var(--orange)}
.services .section-title{top:48px}
.service{position:absolute;top:112px;width:312px;height:402px;text-align:center}
.service--card{background:var(--white);border:1px solid #d6d6d6}
.service__icon{position:absolute;left:84px;top:24px;width:144px;height:144px;border-radius:50%;display:flex;align-items:center;justify-content:center}
.service__icon::before{content:"";position:absolute;inset:6px;border-radius:50%;border:2px solid rgba(255,255,255,.9)}
.service__icon--navy{background:var(--navy)}
.service__icon--orange{background:var(--orange)}
.service__name{position:absolute;left:0;right:0;top:186px;font-size:23px;color:var(--navy)}
.service__text{position:absolute;left:4px;right:4px;top:224px;font-size:15px;line-height:24px;color:var(--text)}
.service .btn{left:73px;top:312px;width:166px;height:50px}

/* quote band */
.quote-band{top:1670px;height:364px;overflow:hidden}
.quote-band__photo{position:absolute;inset:0;background:linear-gradient(100deg,#8a9099 0%,#c9cdd2 25%,#e9e6e3 50%,#d8d4d0 75%,#a6abb2 100%)}
.quote-band__mark{position:absolute;left:622px;top:66px;width:30px;height:38px;background:var(--orange);border-radius:3px}
.quote-band__text{position:absolute;left:140px;right:140px;top:144px;text-align:center;font-size:21px;line-height:38px;color:var(--ink)}
.quote-band .btn{left:542px;top:266px;width:180px;height:60px}

/* portfolio */
.portfolio{top:2034px;height:466px}
.portfolio .section-title{top:50px}
.client-name{position:absolute;left:78px;top:176px;width:270px;font-family:"Open Sans",sans-serif;font-weight:700;font-size:58px;color:var(--pink)}
.project{position:absolute;left:392px;top:142px;width:732px;height:116px;border:1px solid #9a9a9a;padding:22px 26px;font-size:15px;line-height:24px;color:var(--text)}
.testimonial{position:absolute;left:392px;top:280px;width:732px;height:112px;background:var(--dark-box);padding:20px 26px;font-size:15px;line-height:24px;color:var(--white)}
.testimonial cite{font-style:normal;color:var(--orange)}
.testimonial__arrows{position:absolute;right:18px;bottom:18px;display:flex;gap:6px}

/* tech strip */
.tech{top:2500px;height:176px;background:var(--strip-bg);display:flex;align-items:center;justify-content:center;gap:62px}
.tech__name{font-family:"Open Sans",sans-serif;font-weight:700;font-size:28px;color:#6e6e6e}
.badge{width:62px;height:110px;background:#8d8d8d;clip-path:polygon(50% 0,100% 14%,100% 100%,0 100%,0 14%)}
.badge--orange{width:84px;height:84px;background:var(--orange);clip-path:none;border-radius:6px}

/* footer */
.site-footer{top:2676px;height:254px;background:var(--navy);color:var(--white)}
.footer__col{position:absolute;top:40px}
.footer__heading{font-size:21px;color:var(--orange);margin-bottom:20px;padding-left:6px}
.footer__about{left:80px;width:330px;font-size:15px;line-height:23px}
.footer__contact{left:452px;width:330px;font-size:15px;line-height:23px}
.contact-row{display:flex;gap:16px;margin-bottom:20px}
.contact-row svg{flex:none;margin-top:3px}
.footer__news{left:814px;width:296px}
.field{height:40px;background:var(--white);color:#333;font-size:14px;padding:0 14px;display:flex;align-items:center;margin-bottom:10px}
.subscribe{width:194px;height:40px;background:var(--orange);color:var(--white);font-weight:700;font-size:15px;display:flex;align-items:center;justify-content:center;letter-spacing:.5px}
.copyright{position:absolute;left:0;top:2930px;width:1200px;height:50px;background:var(--orange);color:var(--white);font-size:13px;display:flex;align-items:center;justify-content:center}
.copyright b{margin:0 4px}
</style>
</head>
<body>

<header class="hero">
  <div class="hero__photo" role="img" aria-label="Photo of two businessmen in suits smiling while reviewing work at a laptop in a bright office"></div>
  <div class="hero__veil"></div>
  <div class="brand"><span class="brand__mark"></span><span class="brand__name">Kavreo</span></div>
  <nav class="nav"><a class="is-active" href="#">HOME</a><a href="#">TORVISTA</a><a href="#">PORTFOLIO</a><a href="#">CONTACT</a></nav>
  <div class="hero__rule"></div>
  <h1 class="hero__title">HIGH PERFORMANCE <b>TORVISTA</b> SITES:<br>ON TIME AND ON BUDGET</h1>
  <a class="btn">Contact us now</a>
</header>

<section class="welcome">
  <h2 class="welcome__title cond">WELCOME TO <span>KAVREO<br>E-COMMERCE</span></h2>
  <div class="welcome__text">
    <p>Lorem Ipsum is simply dummy text of the printing and typesetting industry. Lorem Ipsum has been the industry's standard dummy text ever since the 1500s</p>
    <p>It has survived not only five centuries, but also the leap into electronic typesetting, remaining essentially unchanged.</p>
  </div>
  <a class="btn">Learn more</a>
  <div class="welcome__photo" role="img" aria-label="Photo of a smiling man in a sweater sitting at a desk beside a desktop computer in an office"></div>
</section>

<section class="services">
  <h2 class="section-title cond">OUR SERVICES</h2>

  <div class="service service--card" style="left:78px">
    <div class="service__icon service__icon--navy">
      <svg width="62" height="62" viewBox="0 0 62 62" fill="none" stroke="#fff" stroke-width="3" stroke-linejoin="round"><path d="M31 6l12 7v14l-12 7-12-7V13z"/><path d="M19 27l12 7v14l-12 7-12-7V34z"/><path d="M43 27l12 7v14l-12 7-12-7V34z"/></svg>
    </div>
    <h3 class="service__name cond">DEVELOPMENT</h3>
    <p class="service__text">Lorem Ipsum is simply dummy text of the printing and typesetting industry. Lorem Ipsum has been the industry's</p>
    <a class="btn">Know more</a>
  </div>

  <div class="service" style="left:444px">
    <div class="service__icon service__icon--orange">
      <svg width="60" height="60" viewBox="0 0 60 60"><circle cx="30" cy="30" r="26" fill="#fff"/><path d="M18 28h7v16h-7z M27 28l7-12c3 0 4 2 3 6l-1 4h8c2 0 3 2 2 4l-4 12c-1 2-2 2-4 2H27z" fill="#e8801e"/></svg>
    </div>
    <h3 class="service__name cond">SUPPORT</h3>
    <p class="service__text">Lorem Ipsum is simply dummy text of the printing and typesetting industry. Lorem Ipsum has been the industry's</p>
    <a class="btn btn--navy">Know more</a>
  </div>

  <div class="service" style="left:812px">
    <div class="service__icon service__icon--navy">
      <svg width="62" height="62" viewBox="0 0 62 62"><circle cx="31" cy="31" r="27" fill="#fff"/><path d="M40 14a10 10 0 0 0-9 14L16 43l4 4 15-15a10 10 0 0 0 13-10l-6 5-5-1-1-5 6-6z" fill="#0d3a6a"/></svg>
    </div>
    <h3 class="service__name cond">MAINTENANCE</h3>
    <p class="service__text">Lorem Ipsum is simply dummy text of the printing and typesetting industry. Lorem Ipsum has been the industry's</p>
    <a class="btn">Know more</a>
  </div>
</section>

<section class="quote-band">
  <div class="quote-band__photo" role="img" aria-label="Close-up photo of hands typing on a laptop keyboard"></div>
  <span class="quote-band__mark"></span>
  <p class="quote-band__text">Lorem Ipsum is simply dummy text of the printing and typesetting industry. Lorem Ipsum has been the industry's standard dummy text ever since the 1500.</p>
  <a class="btn btn--navy">Get a quote</a>
</section>

<section class="portfolio">
  <h2 class="section-title cond">OUR <span>PORTFOLIO</span></h2>
  <div class="client-name">Lumelle</div>
  <div class="project">In the lead-up to the now infamous Snap Rush of 2012, Australia's first landmark national online sales event, Lumelle were looking to fortify their online store-front and ensure it would withstand the upcoming traffic peak for an extended period of time.</div>
  <blockquote class="testimonial">“Bravuln went above and beyond by delivering great work in excellent time frames. I wouldn't hesitate to recommend and I'm looking forward to hiring them again.”<br><cite>- Marcus Delray, Lumelle</cite>
    <div class="testimonial__arrows">
      <svg width="16" height="26" viewBox="0 0 16 26" fill="none" stroke="#aaa" stroke-width="2"><path d="M13 2L3 13l10 11"/></svg>
      <svg width="16" height="26" viewBox="0 0 16 26" fill="none" stroke="#aaa" stroke-width="2"><path d="M3 2l10 11L3 24"/></svg>
    </div>
  </blockquote>
</section>

<section class="tech">
  <span class="tech__name">DataVane</span>
  <span class="tech__name">Torvista</span>
  <span class="tech__name">QRX</span>
  <span class="tech__name">NCB</span>
  <span class="badge"></span>
  <span class="badge badge--orange"></span>
</section>

<footer class="site-footer">
  <div class="footer__col footer__about">
    <h4 class="footer__heading cond">ABOUT US</h4>
    <p>Lorem Ipsum is simply dummy text of the printing and typesetting industry. Lorem Ipsum has been the industry's standard dummy text ever since the 1500s</p>
  </div>
  <div class="footer__col footer__contact">
    <h4 class="footer__heading cond">CONTACT</h4>
    <div class="contact-row">
      <svg width="20" height="18" viewBox="0 0 20 18" fill="#fff"><path d="M10 1L1 9h3v8h5v-5h2v5h5V9h3z"/></svg>
      <span>Suite 42, Level 3|8 Wattlebrook<br>Lane|Fernvale Heights VIC 3999</span>
    </div>
    <div class="contact-row">
      <svg width="20" height="20" viewBox="0 0 20 20" fill="#fff"><path d="M4 1l4 4-2 3c1 3 3 5 6 6l3-2 4 4-3 3C8 19 1 12 1 4z"/></svg>
      <span>1300 648 907</span>
    </div>
    <div class="contact-row">
      <svg width="20" height="16" viewBox="0 0 20 16" fill="none" stroke="#fff" stroke-width="1.6"><rect x="1" y="1" width="18" height="14"/><path d="M1 1l9 8 9-8"/></svg>
      <span>support@kavreo.example</span>
    </div>
  </div>
  <div class="footer__col footer__news">
    <h4 class="footer__heading cond">NEWSLETTER</h4>
    <div class="field">Enter Name</div>
    <div class="field">Enter email</div>
    <div class="subscribe">SUBSCRIBE</div>
  </div>
</footer>
<div class="copyright">© <b>SLATE LINE DESIGN</b> - 2015.All Rights Reserved.</div>

</body>
</html>
```